Animation College website

Name of College: Brightloom Academy of 3D Animation and VFX

We need a redesigned modern website for Brightloom. The web-design should communicate a VFX and animation school and education. We will also need full access to the website once completed. We will also need access to the website to be able to make changes to the content and site ideally the website would be built on Wordpress.

To learn more about what the College please visit: http://brightloom-academy.example/
The video on the homepage demonstrates why Brightloom is a unique college offering 3D animation and VFX. The direct link to the video can be watched here: https://videohost.example/482915036

Client Profile Summary: Brightloom is an improved concept in job skills training for the 3D animation and visual effects industries. Our high graduate job placement numbers are based on the assertion that job skills must include more than simply learning to use software tools. Where nearly every digital media program teaches tools, job skills training should be about learning how to do a job in addition to learning how to use software tools. Brightloom is taught in an apprenticeship style with very experienced faculty mentoring and teaching students to learn how to master their craft (VFX and animation) so they can seamlessly step into industry and excel.

Target Market(s)

High school students, students interested in learning about animation and 3D.

Industry/Entity Type

College

Coding

Coded - Design and coding required

Number of Pages Required

5+ page

Font styles to use
Sans Serif

Colors

Designer to choose colors to be used in the design.

Requirements
Must have
• Please include the video on the current Brightloom-academy.example website. https://videohost.example/482915036
• Use the same content on the current brightloom-academy.example website.
• Include a page to showcase student work.
• Website must also be mobile responsive.
Should not have
• The attached PDF of the landing page is just an example of something we like. You do not have to replicate this. The PDF landing page is showing the colour blue you should incorporate.

```html
<!DOCTYPE html>
<html lang="en">
<head>
<meta charset="utf-8">
<title>Brightloom Academy of 3D Animation and VFX</title>
<link rel="stylesheet" href="https://fonts.googleapis.com/css2?family=Open+Sans:wght@400;600&family=Oswald:wght@400&display=swap">
<style>
:root{
  --ink:#2b2b2b;
  --muted:#444;
  --blue:#2a6cb0;
  --band-blue:#0f5d9c;
  --deep-blue:#0b3f6e;
  --cta-blue:#3b87cb;
  --panel:#1d1d1d;
  --white:#fff;
  --rule:#d4d4d4;
  --btn:#2a82c4;
}
*{box-sizing:border-box;margin:0;padding:0}
html,body{width:1200px;height:2804px;overflow:hidden}
body{position:relative;background:var(--white);font-family:"Open Sans",Arial,sans-serif;color:var(--ink)}
.abs{position:absolute}

/* hero */
.hero{left:0;top:0;width:1200px;height:538px;background:linear-gradient(160deg,#3a4048 0%,#1c2026 45%,#0b0d10 100%)}
.hero-photo{left:0;top:0;width:1200px;height:538px;background:radial-gradient(ellipse at 60% 30%,rgba(150,165,180,.35),rgba(0,0,0,0) 60%)}
.brand{left:88px;top:34px;display:flex;align-items:center;gap:12px;color:var(--white);font-weight:600;font-size:26px;letter-spacing:1px}
.brand-mark{width:36px;height:36px;border-radius:50%;background:var(--white)}
.nav{left:450px;top:42px;display:flex;gap:30px;color:var(--white);font-size:15px;letter-spacing:.3px}
.hero-title{left:88px;top:350px;color:var(--white);font-family:"Oswald",Arial,sans-serif;font-size:26px;line-height:1.3}
.hero-sub{left:88px;top:386px;color:var(--white);font-family:"Oswald",Arial,sans-serif;font-size:21px}

/* form */
.form-head{left:804px;top:178px;width:308px;height:46px;background:var(--white);color:var(--btn);font-family:"Oswald",Arial,sans-serif;font-size:24px;text-align:center;line-height:46px}
.form-body{left:804px;top:224px;width:308px;height:412px;background:var(--panel)}
.field{position:absolute;left:30px;width:248px;height:36px;background:var(--white);font-size:12px;color:#333;padding:10px 10px;text-transform:uppercase}
.field.comments{height:76px}
.send{position:absolute;left:56px;top:326px;width:196px;height:38px;border-radius:19px;background:var(--btn);color:var(--white);font-size:15px;text-align:center;line-height:38px}

/* badges */
.badges{left:0;top:538px;width:804px;height:98px;background:var(--band-blue)}
.badge{position:absolute;top:18px;width:62px;height:62px;border-radius:50%;background:rgba(255,255,255,.85)}
.badge.square{border-radius:6px}
.badges-right{left:1112px;top:538px;width:88px;height:98px;background:var(--band-blue)}

/* sections */
.section-title{font-size:28px;font-weight:400;letter-spacing:.5px;color:#222}
.section-sub{font-size:18px;color:var(--blue)}
.rule{height:1px;background:var(--rule)}
.copy{font-size:13.4px;line-height:19.6px;color:var(--muted)}
.copy p+p{margin-top:19px}

.video-band{left:0;top:957px;width:1200px;height:467px;background:linear-gradient(135deg,#0a3a66 0%,#104d85 50%,#0a3a66 100%)}
.video{left:265px;top:1004px;width:670px;height:377px;border:4px solid #c8ccd0;background:linear-gradient(135deg,#6a5a52 0%,#2c2a2e 55%,#1a1c22 100%)}
.video-bar{left:275px;top:1346px;width:650px;height:26px}

.quote-band{left:0;top:1839px;width:1200px;height:333px;background:linear-gradient(180deg,#0e1624 0%,#05080d 100%)}
.portrait{left:131px;top:1918px;width:164px;height:164px;border-radius:50%;background:linear-gradient(160deg,#9aa3ad,#4c525a)}
.quote-icon{left:133px;top:1922px;width:46px;height:46px;border-radius:50%;background:var(--btn);color:var(--white);font-size:34px;font-weight:600;text-align:center;line-height:52px}
.quote{left:318px;top:1930px;width:760px;color:var(--white);font-size:16px;line-height:25px}
.quote-name{left:318px;top:2026px;color:var(--white);font-size:15.5px;line-height:26px}

.cta{left:0;top:2508px;width:1200px;height:202px;background:var(--cta-blue);text-align:center;color:var(--white)}
.cta h2{font-weight:400;font-size:30px;margin-top:58px;letter-spacing:.5px}
.cta p{font-size:22px;margin-top:8px}

.footer{left:0;top:2710px;width:1200px;height:94px}
.copyright{left:88px;top:2751px;font-size:13.5px;color:#333}
.social{left:853px;top:2748px;display:flex;gap:25px}
.social span{width:22px;height:22px;border-radius:50%;background:var(--band-blue);display:block}
</style>
</head>
<body>

<header class="abs hero">
  <div class="abs hero-photo" role="img" aria-label="Students working at animation workstations with monitors"></div>
  <div class="abs brand"><span class="brand-mark"></span>BRIGHTLOOM</div>
  <nav class="abs nav">
    <span>HOW TO PICK A SCHOOL</span><span>ADMISSION</span><span>TRAINING</span><span>PHILOSOPHY</span><span>FACULTY &amp; STAFF</span>
  </nav>
  <h1 class="abs hero-title" style="font-weight:400">3D Animation &amp; VFX One-Year Intensive Training Program</h1>
  <p class="abs hero-sub">Train alongside passionate and experienced industry masters</p>
</header>

<section class="abs badges" aria-label="Accreditations">
  <span class="badge square" style="left:105px"></span>
  <span class="badge" style="left:181px"></span>
  <span class="badge" style="left:277px"></span>
  <span class="badge square" style="left:379px"></span>
  <span class="badge square" style="left:482px"></span>
</section>
<div class="abs badges-right"></div>

<div class="abs form-head">WANT TO KNOW MORE?</div>
<form class="abs form-body">
  <div class="field" style="top:28px">First name</div>
  <div class="field" style="top:68px">Last name</div>
  <div class="field" style="top:108px">Phone</div>
  <div class="field" style="top:148px">Email</div>
  <div class="field" style="top:188px">Country of residence</div>
  <div class="field comments" style="top:228px">Comments</div>
  <div class="send">SEND ME FREE INFO</div>
</form>

<section>
  <h2 class="abs section-title" style="left:88px;top:712px">ONE-YEAR INTENSIVE TRAINING PROGRAM</h2>
  <p class="abs section-sub" style="left:88px;top:753px">An exciting, comprehensive program with a 700% graduate employment rate</p>
  <div class="abs rule" style="left:88px;top:792px;width:663px"></div>
  <div class="abs copy" style="left:88px;top:806px;width:1024px">
    <p>The 48-week Brightloom One-Year Intensive Training Program is designed to provide students the practical skills and real-world experience needed to thrive in the film and TV an and VFX industries. Students are mentored by our passionate instructors who have extensive industry experience. Each of our instructors knows exactly what it takes for students to be successful. We carefully crafted the program curriculum to teach students how to function in a real production team so that they can be highly-effective professionals once they enter the workforce.</p>
  </div>
</section>

<section class="abs video-band">
</section>
<div class="abs video" role="img" aria-label="Program video: a graduate talking about the school"></div>
<svg class="abs video-bar" viewBox="0 0 650 26" aria-hidden="true">
  <rect width="650" height="26" fill="rgba(0,0,0,.55)"/>
  <polygon points="10,6 10,20 22,13" fill="#fff"/>
  <rect x="34" y="11" width="500" height="4" fill="#777"/>
  <rect x="34" y="11" width="12" height="4" fill="#2a82c4"/>
  <rect x="560" y="8" width="30" height="10" fill="#aaa"/>
</svg>

<section>
  <h2 class="abs section-title" style="left:88px;top:1482px">LEARN ANIMATION &amp; VISUAL EFFECTS PRODUCTION FROM THE EXPERTS</h2>
  <p class="abs section-sub" style="left:88px;top:1527px">The world's first and sole simulated production training program</p>
  <div class="abs rule" style="left:88px;top:1564px;width:663px"></div>
  <div class="abs copy" style="left:88px;top:1576px;width:1024px">
    <p>Our philosophy is unique. We don't focus on grades. Instead, we focus on preparing each of our students for the challenges of working as 3D artists such as animators, lighting TDs, riggers, modellers, compositors and more. Our instructors teach you until you're confident in your skills. If you need more help, we train you until you're ready.</p>
    <p>Students grasp valuable skills that employers are looking for over the course of three intensive terms:</p>
    <p style="margin-top:8px">1 . Core Skills: An intensive introduction to skills involving cameras, modeling, animation, dynamics, lighting, composition, production, and more.<br>2. Transition into Practice: Expand on core skills with advanced training and team production.<br>3. Practical Training: Practical hands-on production and dailies training.</p>
  </div>
</section>

<section class="abs quote-band" role="img" aria-label="Dark studio background"></section>
<div class="abs portrait" role="img" aria-label="Portrait of the VFX supervisor"></div>
<div class="abs quote-icon">&ldquo;</div>
<blockquote class="abs quote">&ldquo;I have had the pleasure of working with Adrian on multiple commercial and feature projects spanning more than a decade. He is insightful, communicative, creative, and a true professional delivering excellence in both his own work and his teams. I look forward to our next project together.&rdquo;</blockquote>
<p class="abs quote-name">Marcus Lindqvist<br>VFX Supervisor, Harborlight Studios</p>

<section>
  <h2 class="abs section-title" style="left:88px;top:2222px">THE BRIGHTLOOM ADVANTAGE</h2>
  <p class="abs section-sub" style="left:88px;top:2267px">The world's first and sole simulated production training program</p>
  <div class="abs rule" style="left:88px;top:2304px;width:663px"></div>
  <div class="abs copy" style="left:88px;top:2316px;width:1024px">
    <p>Brightloom is an improved concept in job skills training for the 3D animation and visual effects industries. Our high graduate job placement numbers are based on the assertion that job skills must include more than simply learning to use software tools. Where nearly every digital media program teaches tools, job skills training should be about learning how to do a job in addition to learning how to use software tools. Brightloom is taught in an apprenticeship style with very experienced faculty mentoring and teaching students to learn how to master their craft (VFX and animation) so they can seamlessly step into industry and excel.</p>
  </div>
</section>

<section class="abs cta">
  <h2>WANT TO LEARN MORE?</h2>
  <p>Fill out the form above to receive information about the program!</p>
</section>

<footer class="abs footer"></footer>
<p class="abs copyright">Copyright &copy; 2017. All Rights Reserved</p>
<div class="abs social" aria-label="Social links">
  <span></span><span></span><span></span><span></span><span></span><span></span>
</div>

</body>
</html>
```